Company Business Card (Company Promotions)

We want a Business Card that is both Elegant & High Class. We want the card stock thick and unique. We want it to build our Brand Name. We service Automobile dealerships & owners who drive luxury & exotic automobiles that cost an average of $75K. We provide towing services for Luxury & Exotic vehicles. Our colors are Black & Construction Yellow (Gold).
We are manufacture certified for Valdora Kent, RQT, PUKA, ELVO, Tavrine, HJ, Colvesi, Pendrel, Casteduvro, Ombra & Sorvanel. We have authorization to use their logo's.
Enclosed is our old business card. We only used the unusual & Unique brands on the cards but are open to the use of all of them. We also use the Federal Competence Badge that identifies our abilities.

Also enclosed is the name font that we use.

Target Market(s)

Business, Executive, Hi end people that drive finer luxury &/or exotic automobiles.

Industry/Entity Type

Business

Contact Information for Business Card

We market our name. Haul Crestmark. Business address is: 4812 Willowmere Lane, NE Ste: 210, Atlanta, GA 30399 Phone: 404-555-0148. Web address is crestmarkhaul-example.com
Manufacture Certified / Nationally Certified

Font styles to use
Other font styles liked:
• AR DESTINE (in Italic's)

Colors
ffc214

Requirements
Must have
• Must have the at least 5 of the manufacture logo's and the Guild Council Emblem (see on other business card)
Nice to have
• Place the manfacture logo's on the back.
Should not have
• No other colors than Black, Yellow & White

```html
<!DOCTYPE html>
<html lang="en">
<head>
<meta charset="utf-8">
<title>Haul Crestmark — Business Card</title>
<link rel="stylesheet" href="https://fonts.googleapis.com/css2?family=Noticia+Text:wght@700&display=swap">
<style>
  :root {
    --gold: #ffc214;
    --black: #111111;
    --carbon: #1c1c1c;
    --white: #ffffff;
    --backdrop: #e9e6df;
  }
  * { box-sizing: border-box; margin: 0; padding: 0; }
  html, body { width: 1200px; height: 892px; overflow: hidden; }
  body {
    background: var(--backdrop);
    display: flex;
    flex-direction: column;
    align-items: center;
    justify-content: center;
    gap: 40px;
    font-family: "Noticia Text", Georgia, serif;
    font-weight: 700;
  }
  .card {
    width: 700px;
    height: 400px;
    position: relative;
    overflow: hidden;
    box-shadow: 0 6px 18px rgba(0,0,0,.25);
  }

  /* Front */
  .card-front { background: linear-gradient(160deg, #262626 0%, var(--carbon) 50%, #0c0c0c 100%); }
  .badge {
    position: absolute; left: 40px; top: 30px;
    width: 96px; height: 96px;
  }
  .wordmark {
    position: absolute; left: 160px; right: 40px; top: 52px;
    color: var(--gold);
    font-size: 46px;
    line-height: 1;
    text-align: center;
    white-space: nowrap;
  }
  .rule-front {
    position: absolute; left: 160px; right: 40px; top: 130px;
    height: 2px; background: var(--gold);
  }
  .tagline {
    position: absolute; left: 150px; right: 30px; top: 142px;
    color: var(--gold); font-size: 17px; text-align: center; letter-spacing: .5px;
  }
  .contact {
    position: absolute; left: 0; right: 0; top: 186px;
    color: var(--gold); text-align: center; font-size: 19px; line-height: 1.35;
    letter-spacing: .5px;
  }
  .contact .address { font-size: 15px; margin-top: 4px; }
  .maker-band {
    position: absolute; left: 0; right: 0; bottom: 0; height: 82px;
    background: var(--white);
    display: flex; align-items: center; justify-content: space-around;
    padding: 0 12px;
  }
  .maker {
    color: var(--black); font-size: 12px; white-space: nowrap;
  }

  /* Back */
  .card-back { background: var(--gold); }
  .back-mark {
    position: absolute; left: 90px; right: 90px; top: 150px;
    color: var(--black);
    font-size: 52px;
    line-height: 1;
    text-align: center;
    white-space: nowrap;
  }
  .rule-back {
    position: absolute; left: 110px; right: 90px; top: 232px;
    height: 2px; background: var(--black);
  }
</style>
</head>
<body>
  <section class="card card-front">
    <svg class="badge" viewBox="0 0 96 96" role="img" aria-label="Federal Competence Badge">
      <circle cx="48" cy="48" r="46" fill="var(--white)"/>
    </svg>
    <h1 class="wordmark">Haul Crestmark</h1>
    <div class="rule-front"></div>
    <p class="tagline">Manufacture Certified / Nationally Certified</p>
    <div class="contact">
      <p>404-555-0148</p>
      <p>404-555-0193</p>
      <p>www.crestmarkhaul-example.com</p>
      <p class="address">4812 Willowmere Lane, NE Ste: 210, Atlanta, GA 30399</p>
    </div>
    <div class="maker-band">
      <span class="maker">Fenmoor</span>
      <span class="maker">RQT</span>
      <span class="maker">Brakstone</span>
      <span class="maker">Pendrel</span>
      <span class="maker">Tavrine</span>
      <span class="maker">Valdora Kent</span>
      <span class="maker">ELVO</span>
      <span class="maker">Trevalle</span>
      <span class="maker">Lynmark</span>
    </div>
  </section>

  <section class="card card-back">
    <p class="back-mark">Haul Crestmark</p>
    <div class="rule-back"></div>
  </section>
</body>
</html>
```